KAJU Freightways #ALLKAJU Business Cards & Letterhead

I am looking to business cards designed for our organization. We are currently undergoing a small re-branding that is taking place. Our organization is called KAJU Freightways and we are headquartered in Phoenix, AZ. We primarily provide transportation and logistics services to the Marlow Parcel Bureau who is our largest customer. I would like to see a design that incorporates name, title, contact info, website, and address (this will be different depending on the employee). I would also like to see some color on the business card using our logo colors or a variation. I would like our logo on the back of the business card with the website displayed. The final design should communicate that we are a next generation transportation operate that focuses on being driver-first, customer-centric, innovative, and sustainable.We would also like our #ALLKAJU catch phrase incorporated as well.

Target Market(s)

Transportation & Logistics

Industry/Entity Type

Trucking Company

Contact Information for Business Card

-First and Last Name
-Position Title
-Contact Phone
-Contact Email
-Physical Address

Font styles to use
Serif

Colors

Designer to choose colors to be used in the design.

Requirements
Must have
• -KAJU logo prominently displayed
• -#ALLKAJU catch phrase used
• -Some amount of color, design gradient, etc.
• -Logo on the back with website listed (https://www.kajufreightco.example)

```html
<!DOCTYPE html>
<html lang="en">
<head>
<meta charset="utf-8">
<title>KAJU Freightways Business Card</title>
<link rel="stylesheet" href="https://fonts.googleapis.com/css2?family=Montserrat:wght@400;500;600;700&display=swap">
<style>
  :root {
    --bg: #e9e7e3;
    --card-white: #ffffff;
    --teal-dark: #0f3542;
    --teal-mid: #1d4f5c;
    --ink: #1f4752;
    --text-grey: #5d6468;
    --green: #6ab04c;
  }
  * { margin: 0; padding: 0; box-sizing: border-box; }
  html, body { width: 1200px; height: 859px; overflow: hidden; }
  body {
    background: var(--bg);
    font-family: "Montserrat", sans-serif;
    position: relative;
  }
  .card {
    position: absolute;
    top: 289px;
    width: 501px;
    height: 285px;
    border-radius: 12px;
    overflow: hidden;
    box-shadow: 0 8px 18px rgba(0,0,0,0.18);
  }
  .card-front { left: 60px; background: var(--card-white); }
  .card-back {
    left: 639px;
    background: radial-gradient(circle at 20% 10%, var(--teal-mid), var(--teal-dark) 75%);
  }
  .ring { position: absolute; inset: 0; }

  .person-name {
    position: absolute; left: 24px; top: 27px;
    font-size: 18.5px; font-weight: 700; color: var(--ink); letter-spacing: 0.3px;
  }
  .person-title {
    position: absolute; left: 24px; top: 46px;
    font-size: 13.5px; font-weight: 400; color: var(--ink);
  }
  .contact-list {
    position: absolute; left: 24px; top: 117px;
    list-style: none;
  }
  .contact-list li {
    display: flex; align-items: center; gap: 7px;
    height: 17px;
    font-size: 13px; color: var(--text-grey);
  }
  .contact-list svg { width: 12px; height: 12px; flex: none; }
  .address {
    position: absolute; left: 24px; top: 184px;
    font-size: 13px; line-height: 15.5px; color: var(--text-grey);
  }
  .hashtag {
    position: absolute; left: 24px; top: 231px;
    font-size: 13px; color: var(--green);
  }
  .hashtag-rule {
    position: absolute; left: 24px; top: 254px;
    width: 11px; height: 2px; background: var(--green);
  }

  .brand-block {
    position: absolute; left: 230px; width: 176px; top: 96px;
    text-align: center; color: #fff;
  }
  .brand-name {
    font-size: 21px; font-weight: 600; letter-spacing: 1px; line-height: 1.25;
  }
  .brand-site {
    margin-top: 12px;
    font-size: 13px; font-weight: 400; letter-spacing: 0.3px;
  }
  .brand-site strong { color: var(--green); font-weight: 600; }
</style>
</head>
<body>
  <section class="card card-front">
    <svg class="ring" viewBox="0 0 501 285" aria-hidden="true">
      <circle cx="502" cy="142" r="140" fill="none" stroke="var(--green)" stroke-width="6"/>
    </svg>
    <h1 class="person-name">DANE HOLLOWAY</h1>
    <p class="person-title">Chairman &amp; CEO</p>
    <ul class="contact-list">
      <li>
        <svg viewBox="0 0 12 12"><circle cx="6" cy="6" r="5" fill="none" stroke="var(--green)" stroke-width="1.2"/><path d="M4 3.5 l1 0 l0.6 1.5 l-0.7 0.6 q0.6 1.3 1.8 1.8 l0.6 -0.7 l1.5 0.6 l0 1 q-3.8 0.4 -4.8 -4.8z" fill="var(--green)"/></svg>
        555-014-2290
      </li>
      <li>
        <svg viewBox="0 0 12 12"><rect x="1" y="2.5" width="10" height="7" fill="none" stroke="var(--green)" stroke-width="1.2"/><path d="M1 2.5 L6 7 L11 2.5" fill="none" stroke="var(--green)" stroke-width="1.2"/></svg>
        info@kajufreightco.example
      </li>
      <li>
        <svg viewBox="0 0 12 12"><circle cx="6" cy="6" r="5" fill="var(--green)"/><path d="M1 6 H11 M6 1 V11 M2 3.5 H10 M2 8.5 H10" stroke="#fff" stroke-width="0.7"/><ellipse cx="6" cy="6" rx="2.3" ry="5" fill="none" stroke="#fff" stroke-width="0.7"/></svg>
        www.kajufreightco.example
      </li>
    </ul>
    <p class="address">4120 North Canyon Ridge<br>Road, Mesa, AZ 85201</p>
    <p class="hashtag">#ALLKAJU</p>
    <span class="hashtag-rule"></span>
  </section>

  <section class="card card-back">
    <svg class="ring" viewBox="0 0 501 285" aria-hidden="true">
      <circle cx="-1" cy="142" r="140" fill="none" stroke="var(--green)" stroke-width="6"/>
    </svg>
    <div class="brand-block">
      <p class="brand-name">KAJU FREIGHTWAYS</p>
      <p class="brand-site">www.<strong>kajufreightco</strong>.example</p>
    </div>
  </section>
</body>
</html>
```